Construction company stationary design

We're wanting to develop a new professional stationary set for a newly establised property related business using our existing logo (attached). Business incorporates renovations, property investment and property development.

Specifically needing letter head, business cards, envelopes, email signature and need to get tshirt and caps embroydered.

Looking for something quite modern but professional using white, black and green.

Investment

```html
<!DOCTYPE html>
<html lang="en">
<head>
<meta charset="utf-8">
<title>Ridgeline Builds – Business Card</title>
<link rel="stylesheet" href="https://fonts.googleapis.com/css2?family=Mulish:wght@400;800&display=swap">
<style>
  :root {
    --bg: #e9e9ec;
    --card: #ffffff;
    --green: #7fba24;
    --green-soft: #93c640;
    --grey-tab: #c4c6c8;
    --text: #8a8b8d;
  }
  * { box-sizing: border-box; margin: 0; padding: 0; }
  html, body { width: 1200px; height: 934px; overflow: hidden; }
  body {
    background: var(--bg);
    font-family: "Mulish", Arial, sans-serif;
    display: flex;
    flex-direction: column;
    align-items: center;
    justify-content: center;
    gap: 40px;
  }
  .card {
    position: relative;
    width: 640px;
    height: 366px;
    background: var(--card);
    overflow: hidden;
    box-shadow: 0 4px 14px rgba(0,0,0,0.08);
  }
  .edge-bar {
    position: absolute; left: 0; top: 168px;
    width: 14px; height: 66px; background: var(--green);
  }
  .card-back .edge-bar { top: 90px; }
  .edge-tab {
    position: absolute; right: 0; top: 70px;
    width: 16px; height: 40px; background: var(--grey-tab);
  }
  .wordmark {
    position: absolute;
    color: var(--green);
    font-weight: 800;
    line-height: 0.95;
    letter-spacing: 0.5px;
    text-transform: uppercase;
  }
  .card-front .wordmark { left: 70px; top: 138px; font-size: 42px; }
  .card-back .wordmark { left: 70px; top: 56px; font-size: 34px; }
  .holder { position: absolute; right: 70px; top: 66px; text-align: right; }
  .holder-name { color: var(--green); font-weight: 800; font-size: 19px; letter-spacing: 0.5px; }
  .holder-role { color: var(--text); font-size: 14px; margin-top: 4px; }
  .contact {
    position: absolute; bottom: 48px;
    color: var(--text); font-size: 13px; line-height: 1.45;
  }
  .contact-address { left: 70px; }
  .contact-online { left: 300px; }
  .contact-phone { left: 466px; }
  .contact-line { display: flex; align-items: center; gap: 7px; }
  .contact-line svg { width: 12px; height: 12px; flex: none; }
  .back-graphic {
    position: absolute;
    left: 250px; right: 0; top: 150px; bottom: 0;
    background: linear-gradient(135deg, var(--green-soft), var(--green));
  }
</style>
</head>
<body>
  <section class="card card-front" aria-label="Business card front">
    <span class="edge-bar"></span>
    <span class="edge-tab"></span>
    <div class="wordmark">Ridgeline<br>Builds</div>
    <div class="holder">
      <div class="holder-name">JORDAN WHITFIELD</div>
      <div class="holder-role">Chief Manager</div>
    </div>
    <div class="contact contact-address">
      <div>418 Aspen Ridge Dr. Suite 210</div>
      <div>Denver, CO 80202</div>
    </div>
    <div class="contact contact-online">
      <div class="contact-line">
        <svg viewBox="0 0 12 12"><rect x="0.5" y="2" width="11" height="8" fill="var(--green)"/><path d="M0.5 2 L6 6.5 L11.5 2" stroke="#fff" fill="none"/></svg>
        info@website.com
      </div>
      <div class="contact-line">
        <svg viewBox="0 0 12 12"><circle cx="6" cy="6" r="5.2" fill="none" stroke="var(--green)" stroke-width="1.3"/><ellipse cx="6" cy="6" rx="2.2" ry="5.2" fill="none" stroke="var(--green)"/><line x1="0.8" y1="6" x2="11.2" y2="6" stroke="var(--green)"/></svg>
        www.website.com
      </div>
    </div>
    <div class="contact contact-phone">
      <div class="contact-line">
        <svg viewBox="0 0 12 12"><rect x="1" y="1" width="10" height="10" rx="2" fill="var(--green)"/><rect x="3" y="3" width="6" height="2" fill="#fff"/></svg>
        (555) 013-2846
      </div>
      <div class="contact-line">
        <svg viewBox="0 0 12 12"><rect x="3" y="0.5" width="6" height="11" rx="1.2" fill="none" stroke="var(--green)" stroke-width="1.4"/><circle cx="6" cy="9.3" r="0.8" fill="var(--green)"/></svg>
        (555) 013-2846
      </div>
    </div>
  </section>

  <section class="card card-back" aria-label="Business card back">
    <div class="back-graphic" role="img" aria-label="Green house silhouette graphic with grey outline"></div>
    <span class="edge-bar"></span>
    <span class="edge-tab"></span>
    <div class="wordmark">Ridgeline<br>Builds</div>
  </section>
</body>
</html>
```